Medical Practice needs a Letterhead Design

We need a clean, modern letterhead design for our stem cell medical practice.

Industry/Entity Type

Medical

```html
<!DOCTYPE html>
<html lang="en">
<head>
<meta charset="utf-8">
<title>Vitacor Medical Letterhead</title>
<link rel="stylesheet" href="https://fonts.googleapis.com/css2?family=Marcellus&display=swap">
<style>
  :root {
    --teal-deep: #36acbf;
    --teal-mid: #7dcbd8;
    --teal-pale: #d9f0f4;
    --paper: #ffffff;
    --navy: #123a4c;
    --glow: rgba(255, 255, 255, 0.8);
  }
  html, body {
    margin: 0;
    padding: 0;
    width: 848px;
    height: 1200px;
    overflow: hidden;
    background: var(--paper);
  }
  .letterhead {
    position: relative;
    width: 848px;
    height: 1200px;
    background: var(--paper);
    overflow: hidden;
  }
  .header-band {
    position: absolute;
    inset: 0 0 auto 0;
    height: 200px;
    background: linear-gradient(to bottom, var(--teal-deep) 0%, var(--teal-mid) 38%, var(--teal-pale) 70%, var(--paper) 96%);
  }
  .header-glow {
    position: absolute;
    left: -30px;
    top: -40px;
    width: 290px;
    height: 250px;
    background: radial-gradient(ellipse at 50% 45%, var(--glow) 0%, rgba(255,255,255,0.45) 40%, rgba(255,255,255,0) 70%);
  }
  .molecule-decor {
    position: absolute;
    left: 266px;
    top: 18px;
    width: 170px;
    height: 165px;
  }
  .helix-decor {
    position: absolute;
    left: 470px;
    top: 0;
    width: 378px;
    height: 195px;
  }
  .brand {
    position: absolute;
    left: 33px;
    top: 28px;
    width: 146px;
    display: flex;
    flex-direction: column;
    align-items: center;
    font-family: "Marcellus", serif;
    color: var(--navy);
  }
  .brand-mark {
    width: 44px;
    height: 44px;
    border-radius: 50%;
    background: var(--navy);
    margin-bottom: 20px;
  }
  .brand-name {
    font-size: 40px;
    line-height: 1;
    letter-spacing: 0.2px;
  }
  .brand-sub {
    margin-top: 6px;
    font-size: 9px;
    line-height: 1;
    letter-spacing: 3px;
  }
</style>
</head>
<body>
  <div class="letterhead">
    <div class="header-band"></div>
    <div class="header-glow"></div>

    <svg class="molecule-decor" viewBox="0 0 170 165" role="img" aria-label="Faint outline molecule pattern of linked hexagons">
      <defs>
        <radialGradient id="moleculeTone" cx="50%" cy="45%" r="60%">
          <stop offset="0%" stop-color="#ffffff" stop-opacity="0.45"/>
          <stop offset="100%" stop-color="#ffffff" stop-opacity="0"/>
        </radialGradient>
      </defs>
      <rect x="0" y="0" width="170" height="165" rx="40" fill="url(#moleculeTone)"/>
    </svg>

    <svg class="helix-decor" viewBox="0 0 378 195" role="img" aria-label="White DNA double helix sweeping across the top right corner">
      <defs>
        <linearGradient id="helixTone" x1="0" y1="0" x2="1" y2="1">
          <stop offset="0%" stop-color="#ffffff" stop-opacity="0.55"/>
          <stop offset="60%" stop-color="#ffffff" stop-opacity="0.35"/>
          <stop offset="100%" stop-color="#ffffff" stop-opacity="0.1"/>
        </linearGradient>
      </defs>
      <path d="M5 0 L150 0 C190 40 260 80 378 95 L378 195 L300 195 C250 150 190 120 120 80 C70 50 25 25 5 0 Z" fill="url(#helixTone)"/>
    </svg>

    <div class="brand">
      <span class="brand-mark"></span>
      <span class="brand-name">Vitacor</span>
      <span class="brand-sub">MEDICAL</span>
    </div>
  </div>
</body>
</html>
```